Cosmetic Supplier Email Campaigns (every 3 weeks)

Looking for a fresh new Mailchimp template to convey the "design agency" feel of our cosmetic development team. Must be great at copywriting and call to action, a love for cosmetics is a plus. We will provide product photography to feature, you can take creative liberties with the imaging and copy. We are looking to send out this email newsletter to the contacts of our sales team every 3 weeks. Template should be consistent, but vary slightly in each campaign to support the feature product and keep things interesting.

Target Market(s)

Marketing, Product Development, Purchasing Professionals in the Cosmetic Industry.

Industry/Entity Type

Cosmetics

Font styles to use
Sans Serif

Colors

Designer to choose colors to be used in the design.

Requirements
Must have
• Clever headline and product copy. Beauty editorial look and feel.

```html
<!DOCTYPE html>
<html lang="en">
<head>
<meta charset="utf-8">
<title>Lumera Beauty – Newsletter</title>
<link rel="stylesheet" href="https://fonts.googleapis.com/css2?family=Lato:wght@400;700&family=Open+Sans:wght@400;600&display=swap">
<style>
  :root {
    --pink: #ee2f6a;
    --pink-light: #fb5f93;
    --pink-deep: #e8205c;
    --ink: #111111;
    --logo-grey: #666666;
    --white: #ffffff;
    --sky: #dbecef;
    --sky-light: #f1f7f8;
    --mist: #e6e6e6;
    --footer-dark: #1e1e1e;
    --footer-light: #eeeeee;
    --text-grey: #444444;
  }
  * { margin: 0; padding: 0; box-sizing: border-box; }
  html, body { width: 1200px; height: 3005px; overflow: hidden; }
  body {
    position: relative;
    background: var(--white);
    font-family: "Open Sans", Arial, sans-serif;
    color: var(--ink);
  }
  .abs { position: absolute; }

  /* Header */
  .masthead { left: 0; top: 0; width: 1200px; height: 165px; background: var(--white);
    display: flex; align-items: center; justify-content: center; }
  .brand-name { font-family: "Lato", Arial, sans-serif; font-weight: 400; font-size: 78px;
    color: var(--logo-grey); letter-spacing: 1px; }

  /* Hero photo */
  .hero-photo { left: 0; top: 165px; width: 1200px; height: 800px;
    background: radial-gradient(circle at 38% 35%, #f4d6cf 0%, #eab7c4 30%, #f1d8e3 55%, #f7efe9 80%); }

  /* Award section */
  .award-backdrop { left: 0; top: 880px; width: 1200px; height: 840px;
    background: linear-gradient(180deg, var(--sky-light) 0%, var(--sky) 60%, #cfe4e9 100%); }
  .hero-wave { left: 0; top: 860px; width: 1200px; height: 120px; }
  .award-title { left: 0; top: 1065px; width: 1200px; text-align: center;
    font-family: "Lato", Arial, sans-serif; font-weight: 400; font-size: 78px; line-height: 1; color: var(--ink); }
  .award-subtitle { left: 0; top: 1155px; width: 1200px; text-align: center;
    font-family: "Lato", Arial, sans-serif; font-weight: 400; font-size: 62px; line-height: 1; color: var(--pink); }
  .award-copy { left: 70px; top: 1258px; width: 1060px; text-align: center;
    font-size: 28px; line-height: 47px; color: var(--ink); }

  .btn { display: flex; align-items: center; justify-content: center;
    font-family: "Open Sans", Arial, sans-serif; color: var(--white); border-radius: 60px; text-decoration: none; }
  .btn-pink { background: linear-gradient(180deg, var(--pink-light) 0%, var(--pink-deep) 100%); }
  .btn-black { background: var(--ink); }
  .award-btn { left: 420px; top: 1430px; width: 372px; height: 104px; font-size: 38px; }

  /* Bokeh section */
  .bokeh-backdrop { left: 0; top: 2100px; width: 1200px; height: 670px;
    background: radial-gradient(circle at 30% 40%, #fafafa 0%, #e9e9e9 50%, #d6d6d6 100%); }

  /* Pink band */
  .pink-band { left: 0; top: 1560px; width: 1200px; height: 680px; }
  .stack-photo { left: 40px; top: 1690px; width: 520px; height: 460px; border-radius: 50%;
    background: radial-gradient(circle, #6e1a22 0%, #2a1012 55%, rgba(20,10,10,0) 72%); }
  .stack-title { left: 612px; top: 1722px; font-size: 60px; color: var(--white); font-weight: 400; }
  .stack-copy { left: 614px; top: 1812px; width: 560px; font-size: 28px; line-height: 46px; color: var(--white); }
  .stack-btn { left: 614px; top: 1976px; width: 288px; height: 82px; font-size: 31px; }

  /* Eyeliner */
  .liner-title { left: 90px; top: 2318px; font-size: 56px; color: var(--pink); font-weight: 400; }
  .liner-copy { left: 92px; top: 2410px; width: 480px; font-size: 24.5px; line-height: 45px; color: var(--ink); }
  .liner-btn { left: 88px; top: 2572px; width: 286px; height: 82px; font-size: 31px; }
  .liner-photo { left: 560px; top: 2270px; width: 600px; height: 430px;
    background: linear-gradient(160deg, rgba(200,140,120,0) 20%, #c99a88 45%, #9a9a9a 65%, rgba(150,150,150,0) 85%); }

  /* Footer */
  .subscribe-bar { left: 0; top: 2766px; width: 1200px; height: 130px; background: var(--footer-dark); }
  .email-field { left: 80px; top: 2792px; width: 1072px; height: 80px; border: 2px solid #8a8a8a; border-radius: 40px;
    display: flex; align-items: center; padding-left: 40px; gap: 18px; color: #d6d6d6; font-size: 28px; }
  .subscribe-btn { left: 938px; top: 2802px; width: 200px; height: 60px; font-size: 28px; background: var(--pink); }
  .legal { left: 0; top: 2896px; width: 1200px; height: 109px; background: var(--footer-light);
    display: flex; align-items: center; justify-content: center; font-size: 25px; color: var(--text-grey); }
</style>
</head>
<body>
  <header class="abs masthead">
    <span class="brand-name">Lumera Beauty</span>
  </header>

  <div class="abs hero-photo" role="img" aria-label="Model wearing a crown of pink and white roses among flowers"></div>

  <div class="abs award-backdrop" role="img" aria-label="Rose petals floating on pale blue water"></div>
  <svg class="abs hero-wave" viewBox="0 0 1200 120" aria-hidden="true">
    <path d="M0,40 C180,10 340,70 520,40 C570,30 590,12 610,10 C640,14 680,50 760,50 C900,50 1050,20 1200,40 L1200,0 L0,0 Z" fill="none"/>
    <path d="M0,40 C180,10 340,70 520,40 C570,30 590,12 610,10 C640,14 680,50 760,50 C900,50 1050,20 1200,40" fill="none" stroke="#ffffff" stroke-width="16"/>
  </svg>

  <h1 class="abs award-title">THE AWARD WINNING</h1>
  <h2 class="abs award-subtitle">COSMETIC PRODUCT</h2>
  <p class="abs award-copy">elementum elit at tellus nec ultricies sit amet porttitor mattis enim In massa libero interdum nec interdum vel blandit sed nulla In ullamcorper est eget tempor cursus neque mi consectetuer mi a ultricies massa</p>
  <a class="abs btn btn-pink award-btn" href="#">Click here</a>

  <div class="abs bokeh-backdrop" role="img" aria-label="Soft white bokeh light background"></div>

  <svg class="abs pink-band" viewBox="0 0 1200 680" aria-hidden="true">
    <defs>
      <linearGradient id="bandFill" x1="0" y1="0" x2="1" y2="1">
        <stop offset="0" stop-color="#ef2d5f"/>
        <stop offset="1" stop-color="#fb5a95"/>
      </linearGradient>
    </defs>
    <path d="M0,20 C250,0 420,80 640,70 C860,60 1000,20 1200,30 L1200,570 C1020,600 880,560 720,620 C620,660 520,680 420,660 C260,630 120,560 0,540 Z" fill="url(#bandFill)"/>
  </svg>

  <div class="abs stack-photo" role="img" aria-label="Stack of round compact pans in red and brown shades"></div>
  <h3 class="abs stack-title">Stackables</h3>
  <p class="abs stack-copy">Elementum elit at tellus nec ultricies sit amet porttitor mattis enim In massa libero interdum nec interdum .</p>
  <a class="abs btn btn-black stack-btn" href="#">Click here</a>

  <h3 class="abs liner-title">Spring Eyeliner</h3>
  <p class="abs liner-copy">Elementum elit at tellus nec ultricies sit amet porttitor mattis enim In massa libero interdum nec interdum .</p>
  <a class="abs btn btn-pink liner-btn" href="#">Click here</a>
  <div class="abs liner-photo" role="img" aria-label="Rose gold and silver liquid eyeliner pens with caps"></div>

  <footer>
    <div class="abs subscribe-bar"></div>
    <div class="abs email-field">
      <svg width="34" height="26" viewBox="0 0 34 26" aria-hidden="true">
        <rect x="1.5" y="1.5" width="31" height="23" rx="3" fill="none" stroke="#d6d6d6" stroke-width="2.5"/>
        <path d="M2,3 L17,15 L32,3" fill="none" stroke="#d6d6d6" stroke-width="2.5"/>
      </svg>
      <span>Email address</span>
    </div>
    <a class="abs btn subscribe-btn" href="#">Subscribe</a>
    <div class="abs legal">© 2018 Company Name&nbsp; All right reserved</div>
  </footer>
</body>
</html>
```